KRT Engineering Business Card Design

We’re looking for an elegant, clean, and timeless business card design that communicates experience, capability, and reliability.

KRT Engineering was established in 1995 , we are a Government Contracting company providing Professional Services to the Office of Frontier Affairs, Harbor Protection and the Vantage Collective. Our capabilities include: Acquisition & Program Management; Intelligence & Security Operations; Cyber, IT & Network Operations; Lifecycle Logistics & Asset Readiness; C5ISR Systems Engineering & Sustainment.

We want the card to reflect a straightforward, confident approach to business. The design should feel polished and professional without being flashy or overly corporate.

Design Direction
Clean, sophisticated, and uncluttered
Elegant but understated
Strong typography and thoughtful spacing
A timeless aesthetic rather than something overly trendy
Confident and established, with a sense of substance
Easy to read and practical in a real-world business setting

The overall impression should be: “These are experienced professionals who know what they’re doing, do what they say, and can be relied upon.”

We’re open to creative interpretations. The finished card should feel distinctive through its typography, proportions, layout, and attention to detail rather than through excessive graphics or visual effects.

We’re looking for a design that would make a potential client immediately feel that they’re dealing with a capable, trustworthy, and established company.

Company Colors: Navy and Gold/Yellow (but you do not need to use these colors on the card)
Company Name: KRT Engineering Associates, Inc. (known as KRT Engineering)
Website: krtengineering.com
Company Logo: Navy & Gold (other variations attached)

```html
<!DOCTYPE html>
<html lang="en">
<head>
<meta charset="utf-8">
<title>KRT Engineering – Business Card</title>
<link rel="stylesheet" href="https://fonts.googleapis.com/css2?family=Poppins:wght@300;400;600;700&display=swap">
<style>
  :root {
    --page-bg: #d9d4cc;
    --navy: #151a3a;
    --navy-deep: #0c1030;
    --gold: #f0c419;
    --gold-deep: #e2a512;
    --frost-top: #eef1f5;
    --frost-bottom: #e3dcdc;
    --text-light: #d8d9e2;
    --logo-navy: #22284a;
  }
  html, body {
    margin: 0;
    padding: 0;
    width: 1200px;
    height: 970px;
    overflow: hidden;
    background: var(--page-bg);
    font-family: "Poppins", sans-serif;
  }
  .card {
    position: absolute;
    left: 80px;
    top: 188px;
    width: 1040px;
    height: 594px;
    border-radius: 30px;
    overflow: hidden;
    box-shadow: 0 18px 40px rgba(0,0,0,0.18);
  }
  .card-shapes {
    position: absolute;
    inset: 0;
    width: 100%;
    height: 100%;
  }
  .brand-name {
    position: absolute;
    left: 110px;
    top: 228px;
    margin: 0;
    font-weight: 700;
    font-size: 112px;
    line-height: 1;
    letter-spacing: -2px;
    color: var(--logo-navy);
  }
  .details {
    position: absolute;
    right: 52px;
    top: 0;
    text-align: right;
    color: var(--text-light);
  }
  .person-name {
    margin: 96px 0 0;
    font-weight: 700;
    font-size: 31px;
    line-height: 1.1;
    color: var(--gold);
  }
  .person-title {
    margin: 2px 0 0;
    font-weight: 400;
    font-size: 25px;
    color: #ffffff;
  }
  .divider {
    width: 118px;
    height: 3px;
    background: var(--gold);
    margin: 36px 0 0 auto;
  }
  .contact-list {
    list-style: none;
    margin: 88px 0 0;
    padding: 0;
  }
  .contact-item {
    display: flex;
    justify-content: flex-end;
    align-items: center;
    gap: 16px;
    font-weight: 300;
    font-size: 26px;
    height: 48px;
  }
  .contact-icon {
    width: 30px;
    height: 30px;
    flex: none;
  }
  .address {
    margin: 60px 0 0;
    font-style: normal;
    font-weight: 300;
    font-size: 25px;
    line-height: 1.4;
  }
</style>
</head>
<body>
  <main class="card">
    <svg class="card-shapes" viewBox="0 0 1040 594" preserveAspectRatio="none" aria-hidden="true">
      <defs>
        <linearGradient id="frost" x1="0" y1="0" x2="0" y2="1">
          <stop offset="0" stop-color="var(--frost-top)"/>
          <stop offset="0.6" stop-color="#e9e8ec"/>
          <stop offset="1" stop-color="var(--frost-bottom)"/>
        </linearGradient>
        <linearGradient id="navy-panel" x1="0" y1="0" x2="1" y2="1">
          <stop offset="0" stop-color="var(--navy)"/>
          <stop offset="1" stop-color="var(--navy-deep)"/>
        </linearGradient>
        <linearGradient id="gold-band" x1="0" y1="0" x2="0" y2="1">
          <stop offset="0" stop-color="var(--gold)"/>
          <stop offset="1" stop-color="var(--gold-deep)"/>
        </linearGradient>
      </defs>
      <rect class="frost-panel" width="1040" height="594" fill="url(#frost)"/>
      <path class="gold-edge" d="M548 150 C 570 320, 500 470, 320 594 L 420 594 C 585 390, 600 200, 548 150 Z" fill="url(#gold-band)"/>
      <path class="navy-panel" d="M500 0 C 600 120, 590 390, 420 594 L 1040 594 L 1040 0 Z" fill="url(#navy-panel)"/>
    </svg>

    <h1 class="brand-name">KRT</h1>

    <section class="details">
      <h2 class="person-name">ALEX MORROW</h2>
      <p class="person-title">Manager</p>
      <div class="divider"></div>
      <ul class="contact-list">
        <li class="contact-item">555-014-2837
          <svg class="contact-icon" viewBox="0 0 30 30" aria-hidden="true"><circle cx="15" cy="15" r="15" fill="var(--gold)"/><path d="M10 8 l3 0 l1.5 4 l-2 1.5 a9 9 0 0 0 4 4 l1.5 -2 l4 1.5 l0 3 a2 2 0 0 1 -2 2 a13 13 0 0 1 -12 -12 a2 2 0 0 1 2 -2 z" fill="var(--navy)"/></svg>
        </li>
        <li class="contact-item">yourname@krtmail.com
          <svg class="contact-icon" viewBox="0 0 30 30" aria-hidden="true"><circle cx="15" cy="15" r="15" fill="var(--gold)"/><rect x="8" y="10" width="14" height="10" rx="1" fill="none" stroke="var(--navy)" stroke-width="1.8"/><path d="M8 10 l7 6 l7 -6" fill="none" stroke="var(--navy)" stroke-width="1.8"/></svg>
        </li>
        <li class="contact-item">www.krtengineering.com
          <svg class="contact-icon" viewBox="0 0 30 30" aria-hidden="true"><circle cx="15" cy="15" r="15" fill="var(--gold)"/><circle cx="15" cy="15" r="8" fill="none" stroke="var(--navy)" stroke-width="1.6"/><ellipse cx="15" cy="15" rx="3.5" ry="8" fill="none" stroke="var(--navy)" stroke-width="1.4"/><path d="M7 15 h16 M8.5 11 h13 M8.5 19 h13" stroke="var(--navy)" stroke-width="1.2"/></svg>
        </li>
      </ul>
      <address class="address">4820 Harbor Lane,<br>Suite 310, Bayview, VA 23999</address>
    </section>
  </main>
</body>
</html>
```